Redesign of LumoWordfind.com in Bootstrap 4

Current design of LumoWordfind.com is not responsive. We need to change it to latest version of Bootstrap 4 keeping essential elements in place.

Apart from home page, we need designs for http://www.lumowordfind.com/meaning/cat also.

Coding

Number of Pages Required

2 page

Colors
34a7d8

Requirements
Must have
• Bootstrap 4

```html
<!DOCTYPE html>
<html lang="en">
<head>
<meta charset="utf-8">
<title>Lumo Wordfind — Home</title>
<link href="https://fonts.googleapis.com/css2?family=Maven+Pro:wght@400;500;700&display=swap" rel="stylesheet">
<style>
:root{
  --brand:#34a7d8;
  --brand-dark:#1f8fc4;
  --accent:#f7931e;
  --ink:#333;
  --muted:#666;
  --line:#e3e3e3;
  --footer:#2b2b2b;
  --footer-text:#bbb;
  --hero-top:#3a3f47;
  --hero-bottom:#2a2622;
}
*{box-sizing:border-box;margin:0;padding:0}
html,body{width:830px;height:1200px;overflow:hidden}
body{font-family:"Maven Pro",Arial,sans-serif;color:var(--ink);background:#fff;position:relative;font-size:9px}
.abs{position:absolute}
.topline{left:0;top:0;width:830px;height:2px;background:var(--brand)}
/* header */
.brand{left:68px;top:26px;font-size:22px;font-weight:700;color:var(--accent);line-height:1}
.brand small{display:block;font-size:10px;color:#1d5d9e;letter-spacing:.5px;margin-top:4px}
.wotd{left:398px;top:28px;width:223px;height:31px;border:2px solid #e6eef2;display:flex;align-items:center;padding-left:10px;font-size:10.5px;color:#444;gap:5px;white-space:nowrap}
.wotd em{font-style:normal;font-size:8px;color:var(--brand)}
.clock{width:9px;height:9px;border:1.5px solid var(--brand);border-radius:50%}
.btn{background:var(--brand);color:#fff;border-radius:3px;display:flex;align-items:center;justify-content:center;font-size:9.5px}
.create{left:629px;top:28px;width:132px;height:30px}
/* nav */
.nav{left:0;top:83px;width:830px;height:41px;background:linear-gradient(#fafafa,#e9e9e9);border-top:1px solid #eee}
.nav a{position:absolute;top:0;height:41px;line-height:44px;font-size:8.5px;color:#444;text-decoration:none;text-align:center}
.nav a.active{background:var(--accent);color:#fff;border-top:4px solid #333;line-height:36px}
/* hero */
.hero{left:0;top:124px;width:830px;height:354px;background:linear-gradient(160deg,var(--hero-top),#4a4038 55%,var(--hero-bottom))}
.hero-art{left:68px;top:28px;width:257px;height:253px;background:linear-gradient(#4f5660,#8b8f94);border-radius:6px;opacity:.85}
.arrow{top:134px;width:12px;height:70px}
.hero-title{left:456px;top:42px;font-size:20px;color:#fff}
.hero-title b{font-weight:700}
.book-mark{left:398px;top:44px;width:48px;height:26px;background:linear-gradient(#fff,#ccc);border-radius:2px;opacity:.9}
.search{left:398px;top:89px;width:274px;height:30px;background:#fff;border:2px solid #8aa;border-radius:3px}
.search span{position:absolute;left:10px;top:9px;font-size:7.5px;color:#777}
.search .go{position:absolute;right:0;top:0;width:37px;height:26px;background:var(--brand)}
.hero h2{position:absolute;left:396px;top:143px;font-size:13.5px;font-weight:400;color:#fff}
.hero ul{position:absolute;left:397px;top:168px;list-style:none;color:#fff;font-size:8.5px}
.hero li{height:23.7px;display:flex;gap:6px}
.hero li i{width:7px;height:7px;background:var(--brand);margin-top:2px;transform:skewX(-12deg)}
/* join */
.join{left:68px;top:440px;width:694px;height:70px;background:#fff;border:1px solid #e2e2e2;box-shadow:0 8px 10px -6px rgba(0,0,0,.25)}
.join .t{position:absolute;left:15px;top:25px;font-size:15px;color:var(--brand);white-space:nowrap}
.join label{position:absolute;top:32px;font-size:7.5px;color:#555;white-space:nowrap}
.join .in{position:absolute;top:23px;height:24px;border:1px solid #ccc;background:#fff}
.join .login{position:absolute;top:23px;left:610px;width:70px;height:24px}
/* features */
.feat-h{left:0;width:830px;top:541px;text-align:center;font-size:20px;color:var(--brand)}
.feat-s{left:0;width:830px;top:570px;text-align:center;font-size:9px;color:var(--muted)}
.card{width:333px;height:140px;border:1px solid var(--line);background:#fff}
.card .img{position:absolute;left:7px;top:7px;width:131px;height:126px}
.card .hd{position:absolute;left:149px;top:7px;width:177px;height:27px;background:var(--brand);color:#fff;font-size:10.5px;padding:7px 8px;white-space:nowrap}
.card .hd:after{content:"";position:absolute;right:8px;top:9px;width:7px;height:7px;border:1px solid #fff}
.card .sub{position:absolute;left:149px;top:44px;color:var(--accent);font-size:8px}
.card p{position:absolute;left:149px;top:60px;width:177px;font-size:7.8px;line-height:14.3px;color:#555}
.card p a{color:var(--brand)}
.card .btn{position:absolute;left:149px;top:109px;width:70px;height:25px}
/* browse */
.browse{left:0;top:951px;width:830px;height:104px;background:linear-gradient(#4fa8d6,#3b97c9)}
.browse h3{position:absolute;left:68px;top:20px;font-size:14.5px;font-weight:400;color:#fff}
.bsearch{position:absolute;left:68px;top:52px;width:242px;height:26px;border:1px solid #fff;color:#eef;font-size:7.5px;font-style:italic;padding:7px 8px}
.bsearch span{position:absolute;right:0;top:0;width:33px;height:24px;background:var(--accent);color:#fff;font-style:normal;text-align:center;line-height:24px}
.divider{position:absolute;left:337px;top:20px;width:1px;height:62px;background:rgba(255,255,255,.6)}
.letters{position:absolute;left:362px;width:380px;display:flex;gap:7.6px}
.letters span{width:16px;height:15px;border:1px solid #fff;color:#fff;font-size:7.5px;text-align:center;line-height:13px}
/* footer */
.footer{left:0;top:1055px;width:830px;height:145px;background:var(--footer);color:var(--footer-text)}
.fcol{position:absolute;top:19px}
.fcol h4{font-size:10px;font-weight:400;color:#fff;margin-bottom:10px}
.fcol ul{list-style:none;font-size:7.8px;line-height:15.5px;float:left;margin-right:40px;white-space:nowrap}
.fcol li:before{content:"▸ ";font-size:6px;margin-right:6px}
.fsep{position:absolute;top:45px;width:1px;height:56px;background:#3f3f3f}
.fbottom{position:absolute;left:68px;top:107px;width:693px;border-top:1px solid #3d3d3d;padding-top:13px;font-size:7.5px;color:#fff;display:flex;justify-content:space-between}
.social{display:flex;gap:4px;align-items:center}
.social i{width:15px;height:15px;display:inline-block}
</style>
</head>
<body>
<div class="abs topline"></div>

<header>
  <div class="abs brand">Lumo<small>WORDFIND</small></div>
  <div class="abs wotd"><span class="clock"></span>Word of the Day! : <em>Tempor incididunt labore.</em></div>
  <div class="abs btn create">✎ Create a New Account</div>
</header>

<nav class="abs nav">
  <a class="active" style="left:68px;width:81px">Home</a>
  <a style="left:198px;width:60px">Idioms</a>
  <a style="left:323px;width:80px">Common Errors</a>
  <a style="left:477px;width:60px">Crossword</a>
  <a style="left:604px;width:50px">Blog</a>
  <a style="left:719px;width:52px">Contact</a>
</nav>

<section class="abs hero">
  <div class="abs hero-art" role="img" aria-label="Desktop computer showing a stack of books on screen"></div>
  <svg class="abs arrow" style="left:34px" viewBox="0 0 12 70"><path d="M10 2 L2 35 L10 68" stroke="#aaa" fill="none"/></svg>
  <svg class="abs arrow" style="left:784px" viewBox="0 0 12 70"><path d="M2 2 L10 35 L2 68" stroke="#aaa" fill="none"/></svg>
  <div class="abs book-mark" role="img" aria-label="Open book"></div>
  <div class="abs hero-title"><b>Lumo</b> English Dictionary</div>
  <div class="abs search"><span>Enter a Word (or) Phrase</span>
    <div class="go"><svg width="37" height="26" viewBox="0 0 37 26"><circle cx="17" cy="12" r="4.5" stroke="#fff" stroke-width="2" fill="none"/><path d="M20.5 15.5 L24 19" stroke="#fff" stroke-width="2"/></svg></div>
  </div>
  <h2>Search, Save and Master Words</h2>
  <ul>
    <li><i></i>Search from more than 300,000 words and phrases</li>
    <li><i></i>Multiple usages to clarify the context</li>
    <li><i></i>Audio, phonetics, meanings, synonyms and antonyms</li>
    <li><i></i>Save the words to your personal deck and access from anywhere</li>
    <li><i></i><u>It's FREE</u></li>
  </ul>
</section>

<form class="abs join">
  <div class="t">Join for FREE!:</div>
  <label style="left:120px">User name:</label>
  <div class="in" style="left:166px;width:192px"></div>
  <label style="left:366px">Password:</label>
  <div class="in" style="left:410px;width:192px"></div>
  <div class="btn login">⊙ Login</div>
</form>

<div class="abs feat-h">Features</div>
<div class="abs feat-s">Sed ut perspiciatis unde omnis iste natus error sit voluptatem accusantium doloremque laudantium, totam rem aperiam, eaque...</div>

<article class="abs card" style="left:68px;top:609px">
  <div class="img" role="img" aria-label="Open book lying on a stack of books" style="background:linear-gradient(#6b4a2e,#c9b9a5 60%,#8a5a36)"></div>
  <div class="hd">English Tidbit</div>
  <div class="sub">gaffe/gaff</div>
  <p><a>"Gaffe"</a> is a social blunder and "gaff" is a large hook. Be warned not to make the gaffe of mixing it up with <a>gaff...</a></p>
  <div class="btn">View more</div>
</article>
<article class="abs card" style="left:428px;top:609px">
  <div class="img" role="img" aria-label="Three coloured puzzle pieces numbered one to three beside step notes" style="background:linear-gradient(90deg,#d9dee3,#f2f2f2)"></div>
  <div class="hd">Daily Crossword</div>
  <div class="sub">Crossword Lovers!</div>
  <p>Take this daily crossword challenge from Lumo Wordfind..</p>
  <div class="btn">Solve Now</div>
</article>
<article class="abs card" style="left:68px;top:778px">
  <div class="img" role="img" aria-label="Browser window showing an addon download page" style="background:linear-gradient(135deg,#1d6fc0,#cfe3f5 60%,#e9eef3)"></div>
  <div class="hd">Blazeview Addon</div>
  <div class="sub">Blazeview</div>
  <p>Add this tool to your Blazeview and quickly look up for definitions from any website without leaving the page...</p>
  <div class="btn">Get it Now!</div>
</article>
<article class="abs card" style="left:428px;top:778px">
  <div class="img" role="img" aria-label="Hand holding a smartphone" style="background:linear-gradient(135deg,#e4e4e2,#a9a39a)"></div>
  <div class="hd">Designed for Pocketphone</div>
  <div class="sub">pocketphone</div>
  <p>Lumo Wordfind is specially designed for your Pocketphone to quickly lookup meaining, usages and audio of words.</p>
  <div class="btn">View more</div>
</article>

<section class="abs browse">
  <h3>Browse Dictionary</h3>
  <div class="bsearch">Type a Word Here...<span>Go!</span></div>
  <div class="divider"></div>
  <div class="letters" style="top:30px"><span>A</span><span>B</span><span>C</span><span>D</span><span>E</span><span>F</span><span>G</span><span>H</span><span>I</span><span>J</span><span>K</span><span>L</span><span>M</span><span>N</span><span>O</span><span>P</span></div>
  <div class="letters" style="top:60px"><span>Q</span><span>R</span><span>S</span><span>T</span><span>U</span><span>V</span><span>W</span><span>X</span><span>Y</span><span>Z</span></div>
</section>

<footer class="abs footer">
  <div class="fcol" style="left:68px"><h4>Home</h4>
    <ul><li>Home</li><li>Idioms</li><li>Common Errors</li></ul>
    <ul><li>Crossword</li><li>Blog</li><li>Contact</li></ul></div>
  <div class="fsep" style="left:240px"></div>
  <div class="fcol" style="left:270px"><h4>LumoWordfind.com</h4>
    <ul><li>FAQ</li><li>Contact</li><li>Blog</li></ul></div>
  <div class="fsep" style="left:390px"></div>
  <div class="fcol" style="left:422px"><h4>Legal</h4>
    <ul><li>Privacy Policy</li><li>Terms of Use</li></ul></div>
  <div class="fsep" style="left:516px"></div>
  <div class="fcol" style="left:545px"><h4>Others</h4>
    <ul><li>Popular Words</li><li>Common Errors in English</li><li>Exam Prep Online</li></ul></div>
  <div class="fsep" style="left:682px"></div>
  <div class="fcol" style="left:714px"><h4>Links</h4>
    <ul><li>Meaning</li><li>Definition</li><li>Phonetics</li></ul></div>
  <div class="fbottom"><span>Copyrights © lumowordfind . 2016 | Allrights reserved.</span>
    <span class="social">Follow With Us: <i style="background:#3b5998"></i><i style="background:#1da1f2"></i><i style="background:#dd4b39"></i><i style="background:#0077b5"></i></span></div>
</footer>
</body>
</html>
```